Elegant, Playful ReDesign of Paperlynx Website in wordpress - Budget has been raised

Project Brief: Paperlynx Website Redesign in WordPress

Introduction: Paperlynx, a cutting-edge document creation solution, aims to revolutionize the tedious process of crafting contracts, offers, forms, and other documents. By saving customers valuable time, streamlining workflows, and minimizing human error, Paperlynx has become an essential tool. As a technology company with a diverse clientele, we're set to boost our online presence through a refreshed WordPress website. Beyond a modernized website, we aspire to establish a stronger brand identity, incorporating graphic elements seamlessly into our online presence.

Current Status: Currently hosted on WordPress, Paperlynx's existing website serves its purpose but is ready for a visual transformation. Our goal is to maintain a modern and attractive appearance while upholding our commitment to simplicity and efficiency. Notably, the website is currently only in Danish. The redesigned structure should include a language switch function to cater to future international customers.

Objectives:
• Modern Aesthetic: Redesign the website with a fresh and modern vibe, reflecting innovation in the document creation sphere.
• User-Friendly: Prioritize an intuitive design for seamless navigation, ensuring visitors easily understand our offerings and benefits.
• Informative Content: Strike a balance between attractiveness and informativeness, clearly communicating Paperlynx's value proposition and simplifying business processes.
• Graphic Elements: Integrate visually appealing graphics that enhance the site's aesthetics and contribute to our overall visual identity. These elements should be versatile for future use in social media, advertisements, and other branding materials.
• Brand Recognition: Maintain our current logo and color scheme while exploring creative ways to establish a distinctive brand identity. The website should be a cornerstone for a cohesive branding strategy.
• Media Integration: Include images or videos on the website to enhance engagement. Find suitable, free-to-use visuals.
• Responsiveness: Ensure the design is responsive and works seamlessly on all devices.
• Demo Booking Form: Improve the design of the form to book a demo.
• Multilingual Support: Enable language transformation; the website is currently in Danish but should cater to other countries.

Guidelines:
• Typography: Up to the designer's discretion.
• Images/Videos: Must be free to use without additional charges.
• WordPress Theme: Use any WordPress theme below $100.
• Logo Redesign: Not needed; stick to the referenced color palette, as our new logo uses these colors.
• Color Palette: Stick to the existing company colors for consistency:
RGB
• #000b3c
• #004c6c
• #319ac3
• Greytones and white are also allowed
• Creativity Encouraged: Embrace creativity within the color palette for the layout, visuals, and overall user experience.

Conclusion: The Paperlynx website redesign marks an exciting opportunity to enhance our online presence. Our goal is to achieve a balance between a modern, attractive design and a clear, informative representation of our innovative solutions. We envision the revamped website as the foundation for a compelling online brand presence, with versatile graphic elements resonating across various digital platforms.

Sections that the website must include: Space for customer logos, space for testimonials, Space and redesign for display of price structure and price comparison, sections for company details and other information.

Design should also include a redesign of the customer cases section.
Generally there should just be a redesign of all things that are on the website.

Link to current website: https://paperlynx.example/

Target Market(s)

+50 employees.

Industry/Entity Type

Document automation

Coding

Coded - Design and coding required

Number of Pages Required

5+ page

Colors
0054AA
0677BA
7BADD7
CADEEF
E8F1F8

Requirements
Must have
• The new webpage must have the same pages as the current one. Frontpage, Book demo, About us, Case stories and Pricing

```html
<!DOCTYPE html>
<html lang="en">
<head>
<meta charset="utf-8">
<title>Paperlynx – Create error-free contracts and quotes quickly</title>
<link href="https://fonts.googleapis.com/css2?family=Roboto:wght@400;500;700&display=swap" rel="stylesheet">
<style>
:root{
  --blue:#319ac3;
  --teal:#004c6c;
  --navy:#000b3c;
  --grey-bg:#f4f4f4;
  --text:#555a66;
  --white:#ffffff;
  --field:#f8f9fb;
  --quote:#c8ccd2;
}
*{margin:0;padding:0;box-sizing:border-box}
html,body{width:1200px;height:5213px;overflow:hidden}
body{position:relative;font-family:"Roboto",Arial,sans-serif;color:var(--text);background:var(--white)}
.abs{position:absolute}
.shapes{position:absolute;left:0;top:0}
/* header */
.brand{left:111px;top:28px;display:flex;align-items:center;gap:12px}
.brand-mark{width:44px;height:44px;background:var(--blue)}
.brand-name{font-size:30px;font-weight:700;color:var(--teal);letter-spacing:.5px}
.main-nav{right:111px;top:38px;display:flex;gap:28px;font-size:14px;color:var(--navy)}
.main-nav .active{color:var(--blue)}
/* hero */
.hero-title{left:111px;top:192px;width:470px;font-size:52px;line-height:52px;font-weight:700;color:var(--navy)}
.hero-list{left:111px;top:372px;list-style:none;font-size:13.5px;line-height:26px;color:var(--navy)}
.hero-list li{display:flex;align-items:center;gap:14px}
.hero-dots{left:121px;top:557px;display:flex;gap:6px}
.hero-dots span{width:12px;height:12px;border-radius:50%;background:#cfd3da}
.hero-dots span:first-child{background:var(--blue)}
.hero-photo{left:640px;top:136px;width:449px;height:416px;border-radius:10px;background:linear-gradient(135deg,#dfe8ee,#b9c6cf 55%,#8a7a6a)}
/* section titles */
.sec-title{left:0;width:1200px;text-align:center;font-size:38px;font-weight:500;color:var(--navy);line-height:46px}
.sec-title.light{color:var(--white)}
.rule{width:58px;height:2px;background:var(--blue);left:571px}
.rule.light{background:#bfe3f2}
/* customers */
.client{width:158px;height:158px;border-radius:50%;background:var(--white);display:flex;align-items:center;justify-content:center;font-size:21px;font-weight:700;color:#333;box-shadow:0 6px 18px rgba(0,0,0,.12)}
.client.ghost{background:rgba(255,255,255,.18);box-shadow:none}
/* testimonials */
.person{background:linear-gradient(160deg,#c9b9a3,#6d6256)}
.person-shadow{background:var(--blue)}
.quote-mark{left:662px;top:1588px}
.quote-text{left:662px;top:1636px;width:420px;font-size:16px;line-height:26px;color:#6b6f78}
.quote-text p+p{margin-top:16px}
.quote-name{left:662px;top:1816px;font-size:25px;font-weight:500;color:var(--navy)}
.quote-role{left:662px;top:1855px;font-size:13px;color:#777}
.arrow-btn{width:36px;height:36px;border-radius:50%;background:var(--white);box-shadow:0 2px 8px rgba(0,0,0,.15);display:flex;align-items:center;justify-content:center}
/* pricing */
.toggle{top:2329px;height:45px;border-radius:23px;border:2px solid var(--blue);font-size:16px;font-weight:500;display:flex;align-items:center;justify-content:center;color:var(--white);width:247px}
.toggle.on{background:var(--blue)}
.plan{top:2426px;width:302px;height:547px;border-radius:40px;background:var(--white);box-shadow:0 10px 30px rgba(0,0,0,.12);text-align:center}
.plan-name{margin-top:44px;font-size:13px;color:#777;letter-spacing:.5px}
.plan-price{margin:12px auto 0;width:253px;height:136px;background:var(--blue);border-radius:6px;color:var(--white);padding-top:18px}
.plan-price strong{display:block;font-size:34px;font-weight:500;line-height:40px}
.plan-price span{display:block;font-size:15px;line-height:30px}
.plan-price .per{font-weight:700;line-height:26px}
.plan ul{list-style:none;margin-top:24px;font-size:16px;color:#666;line-height:42.5px}
.plan-caret{margin-top:4px}
/* demo form */
.field{height:48px;border-radius:24px;background:var(--field);box-shadow:0 4px 14px rgba(0,0,0,.06);font-size:13px;color:#666;padding:0 28px;display:flex;align-items:center}
.field.area{align-items:flex-start;padding-top:20px;border-radius:30px}
.btn{left:514px;top:3507px;width:170px;height:47px;border-radius:24px;background:var(--blue);color:var(--white);font-size:17px;font-weight:500;display:flex;align-items:center;justify-content:center}
/* features */
.features-bg{left:0;top:3655px;width:1200px;height:514px;background:var(--grey-bg);overflow:hidden}
.feature-list{list-style:none;font-size:16px;line-height:25.8px;color:#444}
.video{left:670px;top:3865px;width:419px;height:211px;background:linear-gradient(135deg,#2e4456,#1c2d3b)}
.play{left:855px;top:3946px;width:48px;height:48px;border-radius:50%;background:rgba(255,255,255,.9);display:flex;align-items:center;justify-content:center}
/* about */
.about-photo{left:111px;top:4234px;width:460px;height:460px;border-radius:50%;border:14px solid var(--blue);background:linear-gradient(135deg,#e7e9ec,#a9b0b8)}
.about-title{left:613px;top:4268px;font-size:38px;font-weight:500;color:var(--navy)}
.about-rule{left:615px;top:4340px;width:58px;height:2px;background:var(--blue)}
.about-item .num{position:absolute;left:617px;font-size:40px;color:var(--blue);font-weight:500;line-height:40px}
.about-item h3{position:absolute;left:676px;font-size:16px;font-weight:700;color:var(--navy);line-height:20px}
.about-item p{position:absolute;left:676px;width:400px;font-size:12px;line-height:22px;color:#777}
/* footer */
.foot-nav{left:0;top:4960px;width:1200px;display:flex;justify-content:center;gap:38px;font-size:14px;font-weight:700;color:var(--white)}
.foot-nav .sep{font-weight:400}
.foot-line{left:0;width:1200px;height:1px;background:rgba(255,255,255,.18)}
.contact{display:flex;align-items:center;gap:18px;color:var(--white);font-size:13px;line-height:18px}
.contact b{display:block;font-size:14px}
.contact-icon{width:60px;height:60px;border-radius:50%;border:2px solid var(--blue);display:flex;align-items:center;justify-content:center}
.copy{left:0;top:5156px;width:1200px;text-align:center;font-size:13px;color:var(--white)}
</style>
</head>
<body>

<svg class="shapes" width="1200" height="5213" viewBox="0 0 1200 5213" aria-hidden="true">
  <rect x="593" y="295" width="47" height="57" fill="#319ac3"/>
  <rect x="1089" y="295" width="111" height="57" fill="#319ac3"/>
  <rect x="546" y="376" width="94" height="57" fill="#319ac3"/>
  <rect x="1089" y="376" width="111" height="57" fill="#319ac3"/>
  <rect x="496" y="455" width="144" height="57" fill="#319ac3"/>
  <rect x="1089" y="455" width="111" height="57" fill="#319ac3"/>
  <rect x="0" y="640" width="1200" height="776" fill="#319ac3"/>
  <path d="M0 1416 Q600 1102 1200 1416 L1200 1420 L0 1420 Z" fill="#fff"/>
  <path d="M0 1994 Q600 2296 1200 1994 L1200 2813 L0 2813 Z" fill="#000b3c"/>
  <path d="M0 4696 Q600 4938 1200 4696 L1200 5213 L0 5213 Z" fill="#000b3c"/>
</svg>

<header>
  <div class="abs brand"><span class="brand-mark"></span><span class="brand-name">Paperlynx</span></div>
  <nav class="abs main-nav">
    <span class="active">Home</span><span>Customer cases</span><span>Video</span><span>Live demo</span><span>Prices</span><span>About us</span><span>Book demo</span>
  </nav>
</header>

<section>
  <h1 class="abs hero-title">Create error-free contracts and quotes quickly</h1>
  <ul class="abs hero-list">
    <li><svg width="18" height="16" viewBox="0 0 18 16"><path d="M1 8l5 5L17 2" stroke="#319ac3" stroke-width="3" fill="none"/></svg>Get paragraphs inserted automatically</li>
    <li><svg width="18" height="16" viewBox="0 0 18 16"><path d="M1 8l5 5L17 2" stroke="#319ac3" stroke-width="3" fill="none"/></svg>Get prices calculated automatically</li>
    <li><svg width="18" height="16" viewBox="0 0 18 16"><path d="M1 8l5 5L17 2" stroke="#319ac3" stroke-width="3" fill="none"/></svg>Eliminate manual work</li>
    <li><svg width="18" height="16" viewBox="0 0 18 16"><path d="M1 8l5 5L17 2" stroke="#319ac3" stroke-width="3" fill="none"/></svg>Sign digitally</li>
  </ul>
  <div class="abs hero-dots"><span></span><span></span><span></span></div>
  <div class="abs hero-photo" role="img" aria-label="Photo of a team reviewing a contract together in a bright office"></div>
</section>

<section>
  <h2 class="abs sec-title light" style="top:730px">Our Customers</h2>
  <div class="abs rule light" style="top:780px"></div>
  <div class="abs client ghost" style="left:-95px;top:821px"></div>
  <div class="abs client" style="left:111px;top:821px;font-size:15px">Stratmark</div>
  <div class="abs client" style="left:316px;top:821px;font-size:18px">Lumen Legal</div>
  <div class="abs client" style="left:520px;top:821px;font-size:18px">Dalby Pack</div>
  <div class="abs client" style="left:726px;top:821px;font-size:19px">Webnook</div>
  <div class="abs client" style="left:931px;top:821px;font-size:14px">Quillbox Docs</div>
  <div class="abs client" style="left:111px;top:1000px;font-size:26px">Norvia</div>
  <div class="abs client" style="left:316px;top:1000px">Augeo</div>
  <div class="abs client" style="left:520px;top:1000px;font-size:17px">CloudDesk</div>
  <div class="abs client" style="left:726px;top:1000px;font-size:16px">Klarsyn Law</div>
  <div class="abs client" style="left:931px;top:1000px">Hartwell</div>
  <div class="abs client ghost" style="left:1130px;top:1000px"></div>
</section>

<section>
  <h2 class="abs sec-title" style="top:1374px">Appreciated And<br>Recommended By</h2>
  <div class="abs rule" style="top:1489px"></div>
  <div class="abs person" style="left:111px;top:1532px;width:229px;height:229px" role="img" aria-label="Portrait of a customer"></div>
  <div class="abs person-shadow" style="left:388px;top:1617px;width:136px;height:136px"></div>
  <div class="abs person" style="left:376px;top:1605px;width:136px;height:136px" role="img" aria-label="Portrait of a customer"></div>
  <div class="abs person" style="left:200px;top:1793px;width:136px;height:136px;background:linear-gradient(160deg,#e9ebee,#8f96a3)" role="img" aria-label="Portrait of a customer"></div>
  <div class="abs person" style="left:368px;top:1781px;width:229px;height:231px;background:linear-gradient(160deg,#e6e6e6,#7a7f86)" role="img" aria-label="Portrait of a customer"></div>
  <svg class="abs quote-mark" width="104" height="42" viewBox="0 0 104 42" aria-hidden="true">
    <path d="M22 2 Q2 12 2 38 L22 38 L22 20 L14 20 Q16 10 28 6 Z" fill="#c8ccd2"/>
    <path d="M62 2 Q42 12 42 38 L62 38 L62 20 L54 20 Q56 10 68 6 Z" fill="#c8ccd2"/>
  </svg>
  <div class="abs quote-text">
    <p>I didn't imagine our offer could be fully automated just like that, but we gave it a shot because I saw what others had done with Paperlynx.</p>
    <p>The result has become razor sharp – I am completely happy when I stand with a new offer in my hand.</p>
  </div>
  <div class="abs quote-name">Mikkel Sandholm Larsen</div>
  <div class="abs quote-role">Sales director – Fortline Security</div>
  <div class="abs arrow-btn" style="left:668px;top:1907px"><svg width="12" height="12" viewBox="0 0 12 12"><path d="M8 1L3 6l5 5" stroke="#333" stroke-width="1.6" fill="none"/></svg></div>
  <div class="abs arrow-btn" style="left:719px;top:1907px"><svg width="12" height="12" viewBox="0 0 12 12"><path d="M4 1l5 5-5 5" stroke="#333" stroke-width="1.6" fill="none"/></svg></div>
</section>

<section>
  <h2 class="abs sec-title light" style="top:2234px">Prices</h2>
  <div class="abs rule light" style="top:2298px"></div>
  <div class="abs toggle on" style="left:340px">PAYMENT MONTHLY</div>
  <svg class="abs" style="left:455px;top:2372px" width="16" height="12"><path d="M0 0h16L8 12z" fill="#319ac3"/></svg>
  <div class="abs toggle" style="left:611px">PAYMENT ANNUALLY</div>

  <div class="abs plan" style="left:111px">
    <div class="plan-name">STARTER</div>
    <div class="plan-price"><strong>950 kr.</strong><span class="per">per month</span><span>250 documents / year</span></div>
    <ul><li>1 contract template</li><li>1 user</li><li>+ DKK 95 per additional user</li><li>Export to DOCX</li><li>Export to Pdf</li><li>Own design</li></ul>
    <svg class="plan-caret" width="10" height="6"><path d="M0 0h10L5 6z" fill="#319ac3"/></svg>
  </div>
  <div class="abs plan" style="left:449px">
    <div class="plan-name">PRO</div>
    <div class="plan-price"><strong>1.890 kr.</strong><span class="per">per month</span><span>1000 documents / year</span></div>
    <ul><li>2 contract templates</li><li>1 user</li><li>+ DKK 95 per additional user</li><li>Export to DOCX</li><li>Export to Pdf</li><li>Own design</li></ul>
    <svg class="plan-caret" width="10" height="6"><path d="M0 0h10L5 6z" fill="#319ac3"/></svg>
  </div>
  <div class="abs plan" style="left:785px">
    <div class="plan-name">BUSINESS</div>
    <div class="plan-price"><strong>3.250 kr.</strong><span class="per">per month</span><span>2000 documents / year</span></div>
    <ul><li>4 contract templates</li><li>1 user</li><li>+ DKK 95 per additional user</li><li>Export to DOCX</li><li>Export to Pdf</li><li>Own design</li></ul>
    <svg class="plan-caret" width="10" height="6"><path d="M0 0h10L5 6z" fill="#319ac3"/></svg>
  </div>
</section>

<section>
  <h2 class="abs sec-title" style="top:3055px">Book A Live Demo</h2>
  <div class="abs rule" style="top:3124px"></div>
  <div class="abs field" style="left:208px;top:3169px;width:379px">First name</div>
  <div class="abs field" style="left:611px;top:3169px;width:379px">Last name</div>
  <div class="abs field" style="left:208px;top:3239px;width:379px">Email</div>
  <div class="abs field" style="left:611px;top:3239px;width:379px">Phone</div>
  <div class="abs field area" style="left:208px;top:3319px;width:782px;height:162px">Text here...</div>
  <div class="abs btn">BOOK NOW</div>
</section>

<section>
  <div class="abs features-bg">
    <svg class="abs" style="left:0;top:0" width="1200" height="514"><circle cx="1093" cy="554" r="192" fill="#319ac3"/></svg>
  </div>
  <h2 class="abs sec-title" style="top:3737px">Lots Of Features</h2>
  <div class="abs rule" style="top:3810px"></div>
  <ul class="abs feature-list" style="left:111px;top:3864px">
    <li>Own design</li><li>Calculation of values</li><li>Sections are inserted automatically</li><li>Process for review</li><li>Digital signature</li><li>Lookup in the CVR register</li><li>Global address register</li><li>Download as DOCX</li>
  </ul>
  <ul class="abs feature-list" style="left:447px;top:3864px;width:200px">
    <li>Download as Pdf</li><li>Data in XLSX</li><li>Document designer</li><li>Share with colleagues</li><li>Integration to CRM</li><li>Integration for case management</li><li>More languages</li>
  </ul>
  <div class="abs video" role="img" aria-label="Video thumbnail showing a chalkboard with a headline about creating quotes and contracts quickly"></div>
  <div class="abs play"><svg width="18" height="20" viewBox="0 0 18 20"><path d="M2 1l15 9-15 9z" fill="#1c2d3b"/></svg></div>
</section>

<section>
  <div class="abs about-photo" role="img" aria-label="Photo of hands reviewing charts and documents on a desk"></div>
  <h2 class="abs about-title">About Us</h2>
  <div class="abs about-rule"></div>
  <div class="about-item">
    <span class="num" style="top:4378px">01</span>
    <h3 style="top:4376px">ADVANCED SOFTWARE</h3>
    <p style="top:4409px">We believe that flexible software can change the way contracts are created, allowing them to be created quickly and error-free.</p>
  </div>
  <div class="about-item">
    <span class="num" style="top:4481px">02</span>
    <h3 style="top:4479px">AVAILABILITY</h3>
    <p style="top:4510px">We believe that our service can be built intuitively, so that everyone, regardless of experience, can form contracts of high uniform quality - you become your own lawyer.</p>
  </div>
  <div class="about-item">
    <span class="num" style="top:4610px">03</span>
    <h3 style="top:4608px">GREEN IMPRINT</h3>
    <p style="top:4640px">We believe that the world can be made greener by effectively automating the creation of contracts, so that the need to print completely disappears.</p>
  </div>
</section>

<footer>
  <nav class="abs foot-nav">
    <span>HOME</span><span class="sep">/</span><span>CUSTOMER CASES</span><span class="sep">/</span><span>VIDEO</span><span class="sep">/</span><span>PRICES</span><span class="sep">/</span><span>ABOUT</span>
  </nav>
  <div class="abs foot-line" style="top:5005px"></div>
  <div class="abs contact" style="left:116px;top:5029px">
    <span class="contact-icon"><svg width="22" height="22" viewBox="0 0 24 24"><path d="M6.6 10.8a15 15 0 006.6 6.6l2.2-2.2c.3-.3.7-.4 1-.2 1.1.4 2.3.6 3.6.6.6 0 1 .4 1 1V20c0 .6-.4 1-1 1A17 17 0 013 4c0-.6.4-1 1-1h3.5c.6 0 1 .4 1 1 0 1.3.2 2.5.6 3.6.1.3 0 .7-.2 1z" fill="#319ac3"/></svg></span>
    <div><b>PHONE</b>+1 888 888 8888</div>
  </div>
  <div class="abs contact" style="left:448px;top:5029px">
    <span class="contact-icon"><svg width="20" height="24" viewBox="0 0 20 24"><path d="M10 1a8 8 0 00-8 8c0 6 8 14 8 14s8-8 8-14a8 8 0 00-8-8zm0 11a3 3 0 110-6 3 3 0 010 6z" fill="#319ac3"/></svg></span>
    <div><b>ADDRESS</b>Lorem ipsum dolor sit<br>amet dolor</div>
  </div>
  <div class="abs contact" style="left:812px;top:5029px">
    <span class="contact-icon"><svg width="22" height="16" viewBox="0 0 22 16"><rect x="0" y="0" width="22" height="16" rx="2" fill="#319ac3"/><path d="M1 1l10 8 10-8" stroke="#000b3c" stroke-width="1.8" fill="none"/></svg></span>
    <div><b>EMAIL</b>info@companyname.com</div>
  </div>
  <div class="abs foot-line" style="top:5120px"></div>
  <p class="abs copy">2024 Copyright - <b>Company Name</b> &nbsp;| All Rights Reserved</p>
</footer>

</body>
</html>
```